wealth management firm, professional group, new model

we have a logo that works but we need a card, white background using our colors...clean look

our tag line if can be used in

The Bridge From Client to Owner

```html
<!DOCTYPE html>
<html lang="en">
<head>
<meta charset="utf-8">
<title>Veloro Wealth Partners – Business Card</title>
<link href="https://fonts.googleapis.com/css2?family=Josefin+Sans:wght@400;600;700&display=swap" rel="stylesheet">
<style>
  :root {
    --navy: #06173a;
    --navy-soft: #0f2652;
    --navy-faint: #1a3366;
    --white: #ffffff;
    --paper: #f1f2f4;
    --silver: #d9dde4;
    --ink-grey: #5b6270;
    --backdrop: #e7e8eb;
  }
  * { box-sizing: border-box; margin: 0; padding: 0; }
  html, body {
    width: 1200px; height: 900px; overflow: hidden;
    background: var(--backdrop);
    font-family: "Josefin Sans", sans-serif;
  }
  .canvas { position: relative; width: 1200px; height: 900px; }
  .card {
    position: absolute; left: 320px; width: 560px; height: 320px;
    border-radius: 4px; overflow: hidden;
    box-shadow: 0 10px 30px rgba(6, 23, 58, 0.18);
  }
  .card-back {
    top: 90px; background: var(--navy);
    display: flex; align-items: center; justify-content: center;
  }
  .card-back .brand-faint {
    color: var(--navy-faint); font-weight: 600; font-size: 24px;
    letter-spacing: 0.04em;
  }
  .card-front {
    top: 490px;
    background: linear-gradient(100deg, var(--paper) 0%, var(--white) 70%, var(--paper) 100%);
  }
  .brand {
    position: absolute; top: 30px; left: 0; right: 0; text-align: center;
    color: var(--navy);
  }
  .brand-name {
    display: inline-flex; align-items: center; gap: 10px;
    font-weight: 600; font-size: 26px; letter-spacing: 0.04em;
  }
  .brand-dot {
    width: 12px; height: 12px; border-radius: 50%; background: var(--navy);
  }
  .brand-sub {
    margin-top: 4px; font-weight: 400; font-size: 11px;
    letter-spacing: 0.24em; color: var(--ink-grey);
  }
  .brand-tagline {
    margin-top: 6px; font-weight: 400; font-size: 12px; color: var(--navy);
  }
  .person {
    position: absolute; top: 130px; left: 0; right: 0; text-align: center;
  }
  .person-name {
    font-weight: 700; font-size: 20px; color: var(--navy); letter-spacing: 0.02em;
  }
  .person-role {
    margin-top: 2px; font-weight: 400; font-size: 14px; color: var(--ink-grey);
  }
  .contact-band {
    position: absolute; left: 0; right: 0; bottom: 0; height: 118px;
    background: radial-gradient(ellipse at 50% 60%, var(--navy-soft) 0%, var(--navy) 70%);
    border-top: 5px solid var(--silver);
    color: var(--white); text-align: center;
    padding-top: 18px; font-size: 14px; line-height: 26px;
  }
  .contact-line { display: flex; justify-content: center; align-items: center; gap: 6px; }
  .contact-line svg { width: 13px; height: 13px; fill: none; stroke: var(--white); stroke-width: 1.6; }
  .divider { margin: 0 6px; opacity: 0.8; }
</style>
</head>
<body>
<main class="canvas">
  <section class="card card-back" aria-label="Card back">
    <span class="brand-faint">VELORO</span>
  </section>

  <section class="card card-front" aria-label="Card front">
    <header class="brand">
      <div class="brand-name"><span class="brand-dot"></span>VELORO</div>
      <div class="brand-sub">WEALTH PARTNERS</div>
      <div class="brand-tagline">The Bridge From Client to Owner</div>
    </header>

    <div class="person">
      <div class="person-name">DANIEL REYES</div>
      <div class="person-role">Director</div>
    </div>

    <footer class="contact-band">
      <div class="contact-line">
        <svg viewBox="0 0 16 16" aria-hidden="true"><path d="M3 2h3l1.5 3.5-2 1.2a8 8 0 0 0 3.8 3.8l1.2-2L14 10v3a1 1 0 0 1-1 1A11 11 0 0 1 2 3a1 1 0 0 1 1-1z"/></svg>
        <span>300-555-0142</span>
      </div>
      <div class="contact-line">
        <svg viewBox="0 0 16 16" aria-hidden="true"><rect x="1.5" y="3.5" width="13" height="9"/><path d="M1.5 3.5 8 9l6.5-5.5"/></svg>
        <span>info@velorowealth.com</span>
        <span class="divider">|</span>
        <svg viewBox="0 0 16 16" aria-hidden="true"><circle cx="8" cy="8" r="6.5"/><path d="M1.5 8h13M8 1.5c-3 3.5-3 9.5 0 13M8 1.5c3 3.5 3 9.5 0 13"/></svg>
        <span>www.velorowealth.com</span>
      </div>
      <div class="contact-line"><span>00 dummy city, dummy place 0000</span></div>
    </footer>
  </section>
</main>
</body>
</html>
```